Brindle Sky Port needs a new upscale business card design for our high end aircraft hangar complex

Brindle Sky Port (BSP) is a large, upscale jet hangar complex in the US housing expensive aircraft. We need a new business card design, using our current logo. We will be attending a industry convention and need a card design that will stand out and be remembered by aircraft owners and private pilots.

Target Market(s)

Aircraft pilots or owners looking for a new upscale hangar

Industry/Entity Type

Airport

Contact Information for Business Card

I like to use very heavy card stock, 400#, double sided. Square, no rounded edges please.

Colors
3276b5
0255a3
85abd2

Requirements
Must have
• An expensive, classy design, vivid colors.
Nice to have
• Needs to look very expensive and classy, and have some "pop". Designer must be able to download or copy my current typeface or fonts.
• One card side might be black with the "Logo and Brindle Sky Port Double line image in blue (or try gold, or glossy black), and perhaps have a grayed out "K720 jet silhouette". The other card side would have our contact info, and perhaps the "BSP Logo only". I'd like my contact info 'stacked', not in a paragraph format.
Should not have
• Should not look "too busy". Having a double-sided card will help.

```html
<!DOCTYPE html>
<html lang="en">
<head>
<meta charset="utf-8">
<title>Brindle Sky Port – Business Card</title>
<link href="https://fonts.googleapis.com/css2?family=Montserrat:wght@400;500;700;800&display=swap" rel="stylesheet">
<style>
  :root {
    --backdrop: #2a2b2d;
    --navy: #123a66;
    --navy-deep: #0f3460;
    --sky: #3276b5;
    --paper: #ffffff;
    --ink: #16406e;
  }
  * { margin: 0; padding: 0; box-sizing: border-box; }
  html, body { width: 1200px; height: 900px; overflow: hidden; }
  body {
    background: var(--backdrop);
    font-family: "Montserrat", Arial, sans-serif;
    position: relative;
  }
  .card {
    position: absolute;
    width: 620px;
    height: 354px;
    overflow: hidden;
  }
  /* Back side */
  .card-back {
    left: 150px; top: 90px;
    background: var(--navy);
    color: var(--paper);
  }
  .card-back .brand {
    position: absolute;
    left: 0; right: 0; top: 120px;
    display: flex; align-items: center; justify-content: center; gap: 14px;
  }
  .brand-square {
    width: 30px; height: 30px;
    background: var(--paper);
  }
  .brand-name {
    font-weight: 800;
    font-size: 34px;
    letter-spacing: 1px;
    text-transform: uppercase;
  }
  .card-back .website {
    position: absolute;
    left: 0; right: 0; bottom: 58px;
    text-align: center;
    font-size: 15px;
    letter-spacing: 0.5px;
    font-weight: 400;
  }
  /* Front side */
  .card-front {
    left: 430px; top: 460px;
    background: var(--paper);
    color: var(--ink);
  }
  .card-front .brand {
    position: absolute;
    right: 34px; top: 40px;
    display: flex; align-items: center; gap: 10px;
    color: var(--navy-deep);
  }
  .card-front .brand-square { width: 20px; height: 20px; background: var(--navy-deep); }
  .card-front .brand-name { font-size: 22px; }
  .accent-band {
    position: absolute;
    right: 0; bottom: 0;
    width: 400px; height: 180px;
  }
  .contact {
    position: absolute;
    left: 40px; top: 170px;
  }
  .contact .name {
    font-weight: 700;
    font-size: 24px;
    color: var(--navy-deep);
  }
  .contact .role {
    font-size: 15px;
    color: var(--sky);
    margin-bottom: 10px;
  }
  .contact ul { list-style: none; }
  .contact li {
    display: flex; align-items: center; gap: 12px;
    font-size: 15px;
    line-height: 24px;
    color: var(--ink);
  }
  .contact svg { width: 13px; height: 13px; fill: var(--sky); flex: none; }
</style>
</head>
<body>

  <section class="card card-back">
    <div class="brand">
      <span class="brand-square"></span>
      <span class="brand-name">Brindle Sky Port</span>
    </div>
    <p class="website">www.brindleskyport.com</p>
  </section>

  <section class="card card-front">
    <div class="brand">
      <span class="brand-square"></span>
      <span class="brand-name">Brindle Sky Port</span>
    </div>

    <svg class="accent-band" viewBox="0 0 400 180" preserveAspectRatio="none" aria-hidden="true">
      <polygon points="400,20 400,180 60,180" fill="#123a66"/>
      <polygon points="400,0 400,14 40,180 20,180" fill="#3276b5"/>
    </svg>

    <div class="contact">
      <p class="name">Marlon Whitaker</p>
      <p class="role">Director</p>
      <ul>
        <li>
          <svg viewBox="0 0 24 24"><path d="M6.6 10.8a15.1 15.1 0 0 0 6.6 6.6l2.2-2.2a1 1 0 0 1 1-.25 11.4 11.4 0 0 0 3.6.57 1 1 0 0 1 1 1V20a1 1 0 0 1-1 1A17 17 0 0 1 3 4a1 1 0 0 1 1-1h3.5a1 1 0 0 1 1 1c0 1.25.2 2.45.57 3.57a1 1 0 0 1-.25 1z"/></svg>
          +033 5180-4421
        </li>
        <li>
          <svg viewBox="0 0 24 24"><path d="M3 9c3-4 15-4 18 0l-3 3-3-2V8H9v2l-3 2zM5 14h14v6H5z"/></svg>
          +033 5180-7736
        </li>
        <li>
          <svg viewBox="0 0 24 24"><path d="M2 5h20v14H2zm2 2v.5l8 5 8-5V7zm0 3v7h16v-7l-8 5z"/></svg>
          info@brindleskyport.com
        </li>
        <li>
          <svg viewBox="0 0 24 24"><path d="M12 2a10 10 0 1 0 0 20 10 10 0 0 0 0-20zm0 2c.9 0 2.3 2 2.8 5H9.2C9.7 6 11.1 4 12 4zM4.3 11h4.8c0 1 .1 1.4.2 2H4.3a8 8 0 0 1 0-2zm10.6 0h4.8a8 8 0 0 1 0 2h-5zM9.2 15h5.6c-.5 3-1.9 5-2.8 5s-2.3-2-2.8-5z"/></svg>
          www.brindleskyport.com
        </li>
      </ul>
    </div>
  </section>

</body>
</html>
```